KRV Business Card

Looking for a business card for my restaurant group I own. Four different concepts:

Copperfield Alehouse
Bristow Alehouse
Tanager's Stone Hearth Kitchen
Pellston Patty Company

Card doesn't need to include all the logos.

```html
<!DOCTYPE html>
<html lang="en">
<head>
<meta charset="utf-8">
<title>KRV Business Card</title>
<link href="https://fonts.googleapis.com/css2?family=Open+Sans:wght@400;600;700&display=swap" rel="stylesheet">
<style>
  :root {
    --backdrop: #2c2d30;
    --card: #141415;
    --gold: #d4b06a;
    --white: #f2f2f2;
    --grey: #8a8a8e;
  }
  html, body {
    margin: 0;
    padding: 0;
    width: 1200px;
    height: 900px;
    overflow: hidden;
    background: var(--backdrop);
    font-family: "Open Sans", Arial, sans-serif;
  }
  .canvas {
    position: relative;
    width: 1200px;
    height: 900px;
  }
  .card {
    position: absolute;
    left: 250px;
    width: 700px;
    height: 400px;
    background: var(--card);
    box-shadow: 0 10px 30px rgba(0,0,0,0.45);
  }
  .card--front { top: 36px; }
  .card--back { top: 464px; }

  .brand {
    display: flex;
    align-items: center;
    gap: 12px;
    color: var(--gold);
    font-weight: 600;
    letter-spacing: 0.14em;
    text-transform: uppercase;
  }
  .brand__square {
    width: 14px;
    height: 14px;
    background: var(--gold);
    flex: none;
  }
  .card--front .brand {
    position: absolute;
    left: 0; right: 0; top: 0; bottom: 0;
    justify-content: center;
    font-size: 30px;
  }
  .card--back .brand {
    position: absolute;
    top: 62px;
    right: 52px;
    font-size: 19px;
  }

  .frame {
    position: absolute;
    inset: 18px;
    border: 1.5px solid var(--gold);
  }

  .contact {
    position: absolute;
    left: 70px;
    bottom: 46px;
    color: var(--white);
  }
  .contact__name {
    margin: 0;
    color: var(--gold);
    font-weight: 700;
    font-size: 24px;
    line-height: 1.2;
  }
  .contact__company {
    margin: 2px 0 0;
    font-size: 19px;
    padding-bottom: 10px;
    border-bottom: 2px solid var(--gold);
    display: inline-block;
    padding-right: 30px;
  }
  .contact__list {
    list-style: none;
    margin: 14px 0 0;
    padding: 0;
    font-size: 19px;
    line-height: 1.55;
  }
  .contact__list li {
    display: flex;
    align-items: center;
    gap: 12px;
  }
  .contact__icon {
    width: 15px;
    height: 15px;
    flex: none;
  }
</style>
</head>
<body>
<main class="canvas">
  <section class="card card--front" aria-label="Card front">
    <div class="brand"><span class="brand__square"></span>Kestrel Ridge Ventures</div>
  </section>

  <section class="card card--back" aria-label="Card back">
    <div class="frame"></div>
    <div class="brand"><span class="brand__square"></span>Kestrel Ridge Ventures</div>
    <div class="contact">
      <p class="contact__name">Dean Harlow</p>
      <p class="contact__company">Kestrel Ridge Ventures</p>
      <ul class="contact__list">
        <li>
          <svg class="contact__icon" viewBox="0 0 16 16" aria-hidden="true"><path fill="#d4b06a" d="M3.5 1.5l2.5 0 1 3.5-1.8 1.2a9 9 0 0 0 4.6 4.6L11 9l3.5 1v2.5c0 1-1 2-2 2C6.5 14.5 1.5 9.5 1.5 3.5c0-1 1-2 2-2z"/></svg>
          555-014-2290
        </li>
        <li>
          <svg class="contact__icon" viewBox="0 0 16 16" aria-hidden="true"><rect x="1" y="3" width="14" height="10" fill="#d4b06a"/><path d="M1.5 3.5L8 9l6.5-5.5" fill="none" stroke="#141415" stroke-width="1.4"/></svg>
          dean@krvrestaurants.com
        </li>
        <li>
          <svg class="contact__icon" viewBox="0 0 16 16" aria-hidden="true"><circle cx="8" cy="8" r="7" fill="#d4b06a"/><path d="M1 8h14M8 1c-3 3.5-3 10.5 0 14M8 1c3 3.5 3 10.5 0 14" fill="none" stroke="#141415" stroke-width="1.1"/></svg>
          www.krvrestaurants.com
        </li>
      </ul>
    </div>
  </section>
</main>
</body>
</html>
```